Bookcover: Ways to Turn Into a Bold Pathfinder

I am publishing a super-low-cost innovation book for €4,99 on Quillmere Open Press to help everyone become a great innovator: young ambitious people without college education nor a big budget. Do you want to help me?

Brief:
Design a book cover 1600 x 2560 pixels for QOP.
Main title: Ways to Turn Into a Bold Pathfinder
Sub title: mindset - insights - skills & tools
Author: Joost ter Brakel
Design: captive, and appealing to everyone
Target Group: young ambitious people without college education

For quillmere please format the height/width ratio of 1.6:1

```html
<!DOCTYPE html>
<html lang="en">
<head>
<meta charset="utf-8">
<title>Ways to Turn Into a Bold Pathfinder — Book Cover</title>
<link href="https://fonts.googleapis.com/css2?family=Lato:wght@400;900&family=Roboto:ital,wght@0,500;1,400&display=swap" rel="stylesheet">
<style>
  :root {
    --backdrop: #45c491;
    --cover-light: #fdf0a8;
    --cover-mid: #feeb8c;
    --cover-warm: #fde46a;
    --ink: #111111;
    --teal: #129aa2;
    --teal-soft: #23a6aa;
    --brain-yellow: #fdd65a;
  }
  * { margin: 0; padding: 0; box-sizing: border-box; }
  html, body {
    width: 1200px;
    height: 1200px;
    overflow: hidden;
    background: var(--backdrop);
  }
  .book-cover {
    position: absolute;
    left: 256px;
    top: 50px;
    width: 688px;
    height: 1100px;
    overflow: hidden;
    background: radial-gradient(ellipse at 30% 12%, var(--cover-light) 0%, var(--cover-mid) 55%, var(--cover-warm) 100%);
  }
  .cover-illustration {
    position: absolute;
    left: 20px;
    top: 425px;
    width: 580px;
    height: 675px;
    border-radius: 240px 260px 0 0;
    background:
      radial-gradient(ellipse 46% 30% at 42% 30%, var(--brain-yellow) 0%, var(--brain-yellow) 62%, rgba(253,214,90,0) 100%),
      linear-gradient(200deg, rgba(254,235,140,0) 0%, rgba(254,235,140,0) 60%, var(--brain-yellow) 100%),
      linear-gradient(180deg, var(--teal) 0%, var(--teal-soft) 100%);
  }
  .line {
    position: absolute;
    left: 0;
    width: 100%;
    text-align: center;
    color: var(--ink);
    line-height: 1;
    white-space: nowrap;
  }
  h1 { font-weight: inherit; }
  .title-lead {
    top: 101px;
    font-family: "Lato", sans-serif;
    font-weight: 400;
    font-size: 46px;
  }
  .title-main {
    top: 158px;
    font-family: "Lato", sans-serif;
    font-weight: 900;
    font-size: 120px;
    letter-spacing: 8px;
  }
  .title-main.second {
    top: 277px;
    font-size: 94px;
    letter-spacing: 0;
  }
  .subtitle {
    top: 378px;
    font-family: "Roboto", sans-serif;
    font-weight: 500;
    font-size: 34px;
  }
  .author {
    top: 1011px;
    font-family: "Roboto", sans-serif;
    font-style: italic;
    font-weight: 400;
    font-size: 46px;
  }
</style>
</head>
<body>
  <main class="book-cover">
    <div class="cover-illustration" role="img" aria-label="Illustration of a teal head silhouette with a yellow brain holding a glowing lightbulb, with a column of small doodles of gears, speech bubbles, a megaphone, charts, banknotes and coins beside it"></div>
    <header>
      <p class="line title-lead">WAYS TO TURN INTO</p>
      <h1>
        <span class="line title-main">A BOLD</span>
        <span class="line title-main second">PATHFINDER</span>
      </h1>
      <p class="line subtitle">Mindset - Insights - Skills &amp; Tools</p>
    </header>
    <p class="line author">Joost ter Brakel</p>
  </main>
</body>
</html>
```